Business Card Design For A Renovation Contractor Company

We need a business card for a new company based in Singapore, our company name is "RB Tolvane". We are a renovation contractor that builds designs into reality. We build more of F&B restaurants, retail stores and commercial offices. We work very closely with designers. The final design should communicate to our client that we are a company that you can trust, that will plan and complete your project without giving you a headache. I like my client to remember my company as "RB". The beauty of SIMPLE is important.

Industry/Entity Type

Contractor

Requirements
Nice to have
• Black or Red base

```html
<!DOCTYPE html>
<html lang="en">
<head>
<meta charset="utf-8">
<title>RB Tolvane – Business Card</title>
<link rel="stylesheet" href="https://fonts.googleapis.com/css2?family=Questrial&family=Open+Sans:wght@400;600&display=swap">
<style>
  :root {
    --bg: #3a2a1f;
    --paper: #ffffff;
    --ink: #1f1f1f;
    --red: #ec1c24;
    --charcoal: #3a3a3c;
    --muted: #444444;
    --label: #ffffff;
  }
  * { margin: 0; padding: 0; box-sizing: border-box; }
  html, body { width: 1200px; height: 913px; overflow: hidden; }
  body { background: var(--bg); font-family: "Open Sans", sans-serif; position: relative; }

  .card { position: absolute; width: 465px; height: 265px; overflow: hidden; box-shadow: 0 4px 10px rgba(0,0,0,.45); }
  .card--front { left: 91px; top: 146px; background: var(--paper); }
  .card--back-dark { left: 587px; top: 143px; background: var(--charcoal); }
  .card--back-white { left: 91px; top: 437px; background: var(--paper); }
  .card--back-red { left: 599px; top: 438px; background: var(--red); }

  .label { position: absolute; color: var(--label); font-size: 31px; font-family: "Open Sans", sans-serif; }
  .label--back1 { left: 946px; top: 90px; }
  .label--back2 { left: 128px; top: 735px; }
  .label--back3 { left: 981px; top: 732px; }

  .mark { position: absolute; border-radius: 50%; border: 5px solid var(--red); background: var(--ink); }
  .wordmark { position: absolute; font-family: "Questrial", sans-serif; color: var(--ink); white-space: nowrap; line-height: 1; }
  .tagline { position: absolute; font-family: "Questrial", sans-serif; color: var(--ink); font-size: 14px; border-top: 1px solid var(--ink); padding-top: 1px; white-space: nowrap; }

  .card--front .mark { left: 99px; top: 34px; width: 72px; height: 72px; }
  .card--front .wordmark { left: 28px; top: 111px; font-size: 32px; }
  .card--front .tagline { left: 28px; top: 146px; width: 214px; text-align: center; }

  .contact { position: absolute; left: 297px; top: 33px; font-size: 11.5px; color: var(--muted); line-height: 16px; list-style: none; }
  .contact li { display: flex; align-items: center; gap: 5px; }
  .contact svg { width: 9px; height: 9px; fill: var(--red); flex: none; }
  .address { position: absolute; left: 297px; top: 100px; font-size: 11.5px; color: var(--muted); line-height: 17px; }

  .person { position: absolute; left: 28px; top: 206px; display: flex; align-items: center; white-space: nowrap; }
  .person__name { font-size: 22px; color: var(--red); }
  .person__role { font-size: 14.5px; color: var(--ink); border-left: 1px solid var(--muted); margin-left: 10px; padding-left: 8px; }

  .card--back-dark .mark { left: 157px; top: 55px; width: 150px; height: 150px; border-width: 3px; background: transparent; }

  .card--back-white .mark { left: 191px; top: 55px; width: 72px; height: 72px; }
  .card--back-white .wordmark { left: 0; width: 100%; text-align: center; top: 138px; font-size: 36px; }
  .card--back-white .tagline { left: 110px; width: 245px; top: 181px; text-align: center; font-size: 15px; }

  .ghost-ring { position: absolute; left: 210px; top: 8px; width: 248px; height: 248px; border-radius: 50%; border: 26px solid rgba(120,30,30,.35); }
  .web { position: absolute; left: 38px; top: 226px; font-size: 13px; letter-spacing: 2.5px; color: #2b1a1a; }
</style>
</head>
<body>
  <div class="label label--back1">Back 1</div>
  <div class="label label--back2">Back 2</div>
  <div class="label label--back3">Back 3</div>

  <section class="card card--front" aria-label="Card front">
    <div class="mark" aria-hidden="true"></div>
    <div class="wordmark">RB Tolvane</div>
    <div class="tagline">crafting spaces with purpose</div>
    <ul class="contact">
      <li><svg viewBox="0 0 10 10" aria-hidden="true"><path d="M2 0.5h2l0.8 2.4-1.2 0.9c0.5 1.2 1.4 2.1 2.6 2.6l0.9-1.2 2.4 0.8v2c0 0.6-0.5 1-1 1C4 9 1 6 1 1.5c0-0.5 0.4-1 1-1z"/></svg>012.345.6789</li>
      <li><svg viewBox="0 0 10 10" aria-hidden="true"><path d="M0.5 2h9v6h-9z M0.5 2l4.5 3.5 4.5-3.5" /></svg>info@rbtolvane.com</li>
      <li><svg viewBox="0 0 10 10" aria-hidden="true"><circle cx="5" cy="5" r="4.5"/></svg>www.rbtolvane.com</li>
    </ul>
    <p class="address">Suite 000, RB building,<br>Cityname, country name</p>
    <div class="person"><span class="person__name">Yourname here</span><span class="person__role">Director</span></div>
  </section>

  <section class="card card--back-dark" aria-label="Card back, dark">
    <div class="mark" aria-hidden="true"></div>
  </section>

  <section class="card card--back-white" aria-label="Card back, white">
    <div class="mark" aria-hidden="true"></div>
    <div class="wordmark">RB Tolvane</div>
    <div class="tagline">crafting spaces with purpose</div>
  </section>

  <section class="card card--back-red" aria-label="Card back, red">
    <div class="ghost-ring" aria-hidden="true"></div>
    <div class="web">www.rbtolvane.com</div>
  </section>
</body>
</html>
```